Computer consultant business card

Bexil Software is a newly started computer consulting company. It's a small one-man company that provides mostly Vornix applications but also websites in collaboration with designers. I'm running this company on the side of full time university studies.

I want the final design to be clean and memorable. Be creative! :)

Some inspiration:
http://www.pixelmarta.com/design/48317
http://www.pixelmarta.com/design/2739164/business-card-design-by-frostlynk
http://www.pixelmarta.com/design/604281/business-card-design-by-koralind-vestrabanu

See attachment for my company logo.
Updates

I would like to thank everyone for submitting! I'll need a couple of days to review and ultimately select a design.

Target Market(s)

Non-technical entrepreneurs and small companies.

Industry/Entity Type

University

Requirements
Must have
• My company logo.
In any way, both colors from my logo.
First- and last name, e-mail and phone number.
Double-sided design.
Nice to have
• Something creative with the symbol in my logo

```html
<!DOCTYPE html>
<html lang="en">
<head>
<meta charset="utf-8">
<title>Zelqo Software – Business Card</title>
<link href="https://fonts.googleapis.com/css2?family=Exo+2:wght@400;500&display=swap" rel="stylesheet">
<style>
  :root {
    --page: #e9eaec;
    --card: #ffffff;
    --ink: #333333;
    --blue: #2a7ef0;
    --mist: #e3e8f1;
    --mist-grey: #e2e2e2;
  }
  * { margin: 0; padding: 0; box-sizing: border-box; }
  html, body { width: 1200px; height: 900px; overflow: hidden; }
  body {
    background: var(--page);
    font-family: "Exo 2", sans-serif;
    color: var(--ink);
    position: relative;
  }
  .card {
    position: absolute;
    top: 308px;
    width: 514px;
    height: 284px;
    background: var(--card);
    overflow: hidden;
    box-shadow: 0 2px 6px rgba(0,0,0,0.18);
  }
  .card--front { left: 72px; }
  .card--back { left: 615px; }

  .backdrop-circle {
    position: absolute;
    border-radius: 50%;
  }
  .card--front .backdrop-circle {
    left: -40px; top: -40px; width: 360px; height: 360px;
    background: linear-gradient(160deg, var(--mist-grey) 0%, var(--mist) 60%);
  }
  .card--back .backdrop-circle {
    left: -130px; top: 115px; width: 270px; height: 270px;
    background: linear-gradient(160deg, var(--mist-grey) 0%, var(--mist) 55%);
  }

  .brand {
    position: absolute;
    display: flex;
    align-items: center;
  }
  .brand__dot {
    border-radius: 50%;
    background: var(--blue);
    flex: none;
  }
  .brand__name {
    font-weight: 500;
    color: var(--ink);
    line-height: 1;
    letter-spacing: 1px;
    white-space: nowrap;
  }
  .card--front .brand { left: 90px; top: 92px; }
  .card--front .brand__dot { width: 110px; height: 110px; margin-right: 34px; }
  .card--front .brand__name { font-size: 84px; }

  .card--back .brand { right: 40px; top: 34px; }
  .card--back .brand__dot { width: 70px; height: 70px; margin-right: 22px; }
  .card--back .brand__name { font-size: 54px; }

  .holder {
    position: absolute;
    left: 160px;
    top: 222px;
    font-size: 22px;
    font-weight: 400;
    letter-spacing: 0.5px;
    white-space: nowrap;
  }
  .contacts {
    position: absolute;
    left: 358px;
    top: 225px;
    list-style: none;
    font-size: 15px;
    line-height: 19px;
    white-space: nowrap;
  }
  .contacts li { display: flex; align-items: center; gap: 4px; }
  .contacts svg { width: 11px; height: 11px; fill: var(--blue); }
</style>
</head>
<body>
  <section class="card card--front">
    <div class="backdrop-circle" role="img" aria-label="Faint brand decoration"></div>
    <div class="brand">
      <span class="brand__dot"></span>
      <span class="brand__name">zelqo</span>
    </div>
  </section>

  <section class="card card--back">
    <div class="backdrop-circle" role="img" aria-label="Faint brand decoration"></div>
    <div class="brand">
      <span class="brand__dot"></span>
      <span class="brand__name">zelqo</span>
    </div>
    <p class="holder">Marten Oskal</p>
    <ul class="contacts">
      <li>
        <svg viewBox="0 0 24 24" aria-hidden="true"><path d="M6.6 10.8a15.1 15.1 0 0 0 6.6 6.6l2.2-2.2c.3-.3.7-.4 1-.2 1.1.4 2.3.6 3.6.6.6 0 1 .4 1 1V20c0 .6-.4 1-1 1A17 17 0 0 1 3 4c0-.6.4-1 1-1h3.5c.6 0 1 .4 1 1 0 1.3.2 2.5.6 3.6.1.3 0 .7-.2 1z"/></svg>
        <span>5550 123 456</span>
      </li>
      <li>
        <svg viewBox="0 0 24 24" aria-hidden="true"><path d="M2 5h20v14H2z M2 5l10 8 10-8" stroke="#fff" stroke-width="1.5"/></svg>
        <span>hello@zelqo.com</span>
      </li>
    </ul>
  </section>
</body>
</html>
```